Velmarotix - world unique technology for better life - please let them know who am i at first sight

We need a new business card for company which is a provider of unique crystal based technology suitable for all living being. For more information and final design you can use our brochure (our colours are black and blue from brochure).
We use Verdana font

Industry/Entity Type

Business

Contact Information for Business Card

regular dimension

Font styles to use
Other font styles liked:
• Verdana

Requirements
Must have
• Logo
• name
• function/position
• phone
• mobile
• e-mail
• adress
Nice to have
• inovative design (technology directed)

```html
<!DOCTYPE html>
<html lang="en">
<head>
<meta charset="utf-8">
<title>Velmarotix Technologies – Business Card</title>
<link rel="stylesheet" href="https://fonts.googleapis.com/css2?family=Open+Sans:wght@300;400;700&display=swap">
<style>
  :root {
    --ink: #0b0b0c;
    --brand-blue: #1aa6e4;
    --silver: #b9bcc0;
    --white: #ffffff;
    --stage: #e9eaec;
    --card-font: "Open Sans", Verdana, sans-serif;
  }
  * { box-sizing: border-box; margin: 0; padding: 0; }
  html, body { width: 1200px; height: 948px; overflow: hidden; }
  body {
    background: var(--stage);
    font-family: var(--card-font);
    position: relative;
  }
  .card {
    position: absolute;
    overflow: hidden;
    box-shadow: 0 10px 30px rgba(0,0,0,.18);
  }
  /* Front */
  .card-front {
    left: 70px; top: 302px;
    width: 600px; height: 343px;
    background: var(--ink);
    color: var(--white);
  }
  .card-front .waves { position: absolute; inset: 0; }
  .brand {
    position: absolute; right: 34px; top: 70px;
    display: flex; align-items: center; gap: 14px;
  }
  .brand-dot {
    width: 54px; height: 54px; border-radius: 50%;
    background: var(--brand-blue);
  }
  .brand-name {
    font-size: 34px; font-weight: 300; letter-spacing: 1px;
    color: var(--brand-blue);
  }
  .person { position: absolute; left: 34px; top: 134px; }
  .person-name { font-size: 22px; font-weight: 700; color: var(--brand-blue); }
  .person-role { font-size: 14px; font-weight: 400; margin-top: 2px; }
  .contacts {
    position: absolute; right: 40px; top: 170px;
    list-style: none; font-size: 12.5px; line-height: 22px;
  }
  .contacts li { display: flex; align-items: center; gap: 8px; }
  .contacts svg { width: 14px; height: 14px; flex: none; }
  .address {
    position: absolute; left: 34px; bottom: 16px;
    font-size: 12.5px; color: var(--white);
  }
  /* Back */
  .card-back {
    left: 770px; top: 174px;
    width: 343px; height: 600px;
    background: var(--brand-blue);
    color: var(--white);
  }
  .back-url {
    position: absolute; left: 36px; top: 120px;
    writing-mode: vertical-rl;
    font-size: 14px; font-weight: 700; letter-spacing: 3px;
  }
  .back-mark {
    position: absolute; left: 50%; top: 50%;
    transform: translate(-50%, -50%);
    display: flex; flex-direction: column; align-items: center; gap: 18px;
  }
  .back-mark .brand-dot { width: 150px; height: 150px; background: var(--white); }
  .back-mark .brand-name { color: var(--white); font-size: 28px; }
</style>
</head>
<body>
  <section class="card card-front" aria-label="Business card front">
    <svg class="waves" viewBox="0 0 600 343" width="600" height="343" aria-hidden="true">
      <path d="M0 0 H600 V14 C440 14 300 118 0 92 Z" fill="var(--brand-blue)"/>
      <path d="M600 24 C440 24 300 128 0 104" fill="none" stroke="var(--silver)" stroke-width="7"/>
      <path d="M600 32 C440 32 300 136 0 113" fill="none" stroke="var(--white)" stroke-width="1.5"/>
      <path d="M0 343 V300 C160 318 320 262 600 300 V343 Z" fill="var(--brand-blue)"/>
      <path d="M0 292 C160 310 320 254 600 292" fill="none" stroke="var(--silver)" stroke-width="5"/>
    </svg>

    <div class="brand">
      <span class="brand-dot"></span>
      <span class="brand-name">VELMAROTIX</span>
    </div>

    <div class="person">
      <p class="person-name">Mira Lendvai</p>
      <p class="person-role">Founder and CEO</p>
    </div>

    <ul class="contacts">
      <li>
        <svg viewBox="0 0 16 16"><circle cx="8" cy="8" r="8" fill="var(--brand-blue)"/><path d="M5 4.5 L6.6 4.3 L7.3 6.2 L6.4 7 C6.9 8.2 7.8 9.1 9 9.6 L9.8 8.7 L11.7 9.4 L11.5 11 C8 11.3 4.7 8 5 4.5Z" fill="var(--white)"/></svg>
        012-555-0147
      </li>
      <li>
        <svg viewBox="0 0 16 16"><circle cx="8" cy="8" r="8" fill="var(--brand-blue)"/><rect x="5.5" y="3.5" width="5" height="9" rx="1" fill="var(--white)"/><rect x="6.3" y="4.6" width="3.4" height="5.6" fill="var(--brand-blue)"/></svg>
        012-555-0148
      </li>
      <li>
        <svg viewBox="0 0 16 16"><circle cx="8" cy="8" r="8" fill="var(--brand-blue)"/><rect x="4" y="5" width="8" height="6" fill="var(--white)"/><path d="M4 5 L8 8.5 L12 5" fill="none" stroke="var(--brand-blue)" stroke-width="1"/></svg>
        info@velmarotix.cu
      </li>
      <li>
        <svg viewBox="0 0 16 16"><circle cx="8" cy="8" r="8" fill="var(--brand-blue)"/><circle cx="8" cy="8" r="4.2" fill="none" stroke="var(--white)" stroke-width="1.1"/><path d="M3.8 8 H12.2 M8 3.8 V12.2" stroke="var(--white)" stroke-width="1"/></svg>
        www.velmarotix.cu
      </li>
    </ul>

    <p class="address">Street Name, City Name, Zipcode-01234</p>
  </section>

  <section class="card card-back" aria-label="Business card back">
    <p class="back-url">www.velmarotix.cu</p>
    <div class="back-mark">
      <span class="brand-dot"></span>
      <span class="brand-name">VELMAROTIX</span>
    </div>
  </section>
</body>
</html>
```